New Business card design to reflect rebrand

I would like a business card design with a good base colour for our new logo and also a placeholder for a profile pic of the card holder. the design needs to be editable to the point that we can easily change the picture of the person and use that design for printmerlo etc. we are looking at a metalic finish business card so will need a good base colour to bring out the finish.

Target Market(s)

prospective customers

Industry/Entity Type

Business

Contact Information for Business Card

I would like one editable design that we can change the name of the card holder and profile picture. The design need to be in a format that be send to printmerlo etc.

Our address is Fenwick Lodge, Copse Lane, Ashwell Green, GU14 3TP Tel no. 01483 556172

Requirements
Must have
• place holder for a profile pic for the card holder. in AI or preferably PSD format

```html
<!DOCTYPE html>
<html lang="en">
<head>
<meta charset="utf-8">
<title>Brightmoor Workplace Services – Business Card</title>
<link rel="stylesheet" href="https://fonts.googleapis.com/css2?family=Michroma&family=Montserrat:wght@400;500;700&display=swap">
<style>
  :root {
    --navy: #3d5475;
    --orange: #f26522;
    --white: #ffffff;
    --ink: #3a4a63;
    --stage: #2a2a2c;
    --photo-light: #d9c7bd;
    --photo-dark: #2b2f3a;
  }
  * { box-sizing: border-box; margin: 0; padding: 0; }
  html, body {
    width: 1200px; height: 900px; overflow: hidden;
    background: var(--stage);
  }
  .canvas { position: relative; width: 1200px; height: 900px; }

  .card {
    position: absolute;
    width: 600px; height: 343px;
    border-radius: 18px;
    overflow: hidden;
    box-shadow: 0 14px 30px rgba(0,0,0,.45);
  }
  .card-shapes { position: absolute; inset: 0; width: 100%; height: 100%; }

  /* Front */
  .card-front { left: 110px; top: 90px; background: var(--navy); }
  .brand-block {
    position: absolute; left: 0; right: 0; top: 108px;
    text-align: center;
  }
  .brand-name {
    font-family: "Michroma", sans-serif;
    color: var(--white);
    font-size: 40px; letter-spacing: 2px; line-height: 1.1;
  }
  .brand-tagline {
    font-family: "Michroma", sans-serif;
    color: var(--white);
    font-size: 15px; letter-spacing: 6px; margin-top: 8px;
  }
  .front-web {
    position: absolute; right: 34px; top: 212px;
    font-family: "Montserrat", sans-serif; font-weight: 500;
    font-size: 13px; color: var(--orange);
  }

  /* Back */
  .card-back { left: 490px; top: 470px; background: var(--white); }
  .photo-slot {
    position: absolute; left: 70px; top: 118px;
    width: 260px; height: 240px;
    border-radius: 120px 120px 0 0;
    background: linear-gradient(180deg, var(--photo-light) 0%, #b89c8e 45%, var(--photo-dark) 100%);
    clip-path: polygon(0 0, 100% 0, 100% 176px, 0 242px);
  }
  .back-brand {
    position: absolute; right: 36px; top: 34px;
    font-family: "Michroma", sans-serif;
    font-size: 30px; color: var(--navy); letter-spacing: 1px;
  }
  .holder {
    position: absolute; left: 330px; top: 98px;
  }
  .holder-name {
    font-family: "Michroma", sans-serif;
    font-size: 19px; color: var(--orange); letter-spacing: 1px;
  }
  .holder-role {
    font-family: "Montserrat", sans-serif; font-weight: 700;
    font-size: 12px; color: var(--ink); letter-spacing: 1px; margin-top: 2px;
  }
  .contact-list { list-style: none; margin-top: 12px; }
  .contact-list li {
    display: flex; align-items: center; gap: 8px;
    font-family: "Montserrat", sans-serif; font-size: 12px; color: var(--ink);
    line-height: 19px;
  }
  .contact-list svg { width: 11px; height: 11px; flex: none; }
  .web-accent { color: var(--orange); font-weight: 700; }
  .address {
    font-family: "Montserrat", sans-serif; font-size: 12px; color: var(--ink);
    line-height: 17px; margin-top: 10px;
  }
</style>
</head>
<body>
<main class="canvas">

  <section class="card card-front" aria-label="Business card front">
    <svg class="card-shapes" viewBox="0 0 600 343" preserveAspectRatio="none" aria-hidden="true">
      <polygon points="0,296 300,296 322,318 600,252 600,343 0,343" fill="var(--white)"/>
      <polygon points="322,305 600,240 600,252 322,318" fill="var(--orange)"/>
    </svg>
    <div class="brand-block">
      <div class="brand-name">BRIGHTMOOR</div>
      <div class="brand-tagline">WORKPLACE SERVICES</div>
    </div>
    <div class="front-web">www.brightmoor.com</div>
  </section>

  <section class="card card-back" aria-label="Business card back">
    <div class="photo-slot" role="img" aria-label="Profile photo of the card holder"></div>
    <svg class="card-shapes" viewBox="0 0 600 343" preserveAspectRatio="none" aria-hidden="true">
      <polygon points="480,262 600,228 600,343 470,343" fill="var(--navy)"/>
      <polygon points="150,343 470,262 480,262 480,272 190,343" fill="var(--orange)"/>
    </svg>
    <div class="back-brand">BRIGHTMOOR</div>
    <div class="holder">
      <div class="holder-name">MARCUS ELLERY</div>
      <div class="holder-role">DIRECTOR</div>
      <ul class="contact-list">
        <li>
          <svg viewBox="0 0 12 12"><path d="M3 1 L5 3.5 L4 5 Q5 7 7 8 L8.5 7 L11 9 L9.5 11 Q4 10.5 1 3 Z" fill="var(--orange)"/></svg>
          01483 556172
        </li>
        <li>
          <svg viewBox="0 0 12 12"><rect x="1" y="2.5" width="10" height="7" fill="none" stroke="var(--orange)" stroke-width="1.3"/><path d="M1 2.5 L6 6.5 L11 2.5" fill="none" stroke="var(--orange)" stroke-width="1.3"/></svg>
          info@brightmoor.com
        </li>
        <li>
          <svg viewBox="0 0 12 12"><circle cx="6" cy="6" r="5" fill="none" stroke="var(--orange)" stroke-width="1.2"/><path d="M1 6 H11 M6 1 Q3 6 6 11 M6 1 Q9 6 6 11" fill="none" stroke="var(--orange)" stroke-width="1"/></svg>
          <span>www.<span class="web-accent">brightmoor</span>.com</span>
        </li>
      </ul>
      <p class="address">Fenwick Lodge, Copse Lane<br>Ashwell Green, GU14 3TP</p>
    </div>
  </section>

</main>
</body>
</html>
```